Counseling Practice Business Card

I need a professional looking business card incorporating my new logo that was just completed. Card needs to incorporate my name and title, description of my specialty, my address, my phone number, my fax number, my email and my website URL. I need to be able to choose design on/with different paper colors and textures.
I do not have a lot of business card ideas so I am open to anything but I want bold,sharp, clear card without additional designs other than my logo (see attached file info). I am open to different color backgrounds or paper colors including black. I do not like traditional brackets around area codes in phone number or dashes between numbers in phone number. Am open to other ways of presenting including periods between numbers as appropriate. I do not know enough to know what I like yet but I want card to coordinate and work together with my logo. My practice emphasizes natural mental health interventions so any use of color (with background paper color or the blue and green in my logo) that elicits nature is nice. In addition to black, any natural brown or wood looking background might be desirable also. Most of the offerings so far look very similar and boring.

Target Market(s)

Potential therapy clients and other professionals

Contact Information for Business Card

Card information:
Gerald M. Whitcombe, Ph.D.
Licensed Clinical Psychologist
Integrative Health Coach
4812 Marlowe Ridge Blvd SE
Suite 310
Duluth, GA 30096
(770) 415-2983 phone
(770) 581-4096 fax
drgeraldwhitcombe@quillmarsh.net
brightfernwellness.net

Font styles to use
Serif
Sans Serif
Other font styles liked:
• anything that you think looks crisp, clear and easily readable

Requirements
Must have
• Any color used should coordinate with my logo design (see attached files).
• Card should be printed horizontally so top and bottom are longest sides of rectangle.
• Background color or paper color should complement and highlight logo. Do not like a white background. black, grey, brown or any color my logo would blend well with.
Nice to have
• I would like designer to utilize color to highlight letters/name or phone-fax-web symbols.
• Bottom edge of card could be highlighted if appropriate to an idea.
Should not have
• I would NOT want the card to have a pure white background at all.
• No clear cards.
• Cards should be oriented with long sides on bottom and top, NOT sides. DO NOT LIKE THIS THIN TALL ORIENTATION.

```html
<!DOCTYPE html>
<html lang="en">
<head>
<meta charset="utf-8">
<title>Brightfern Counseling – Business Card</title>
<link href="https://fonts.googleapis.com/css2?family=Lato:wght@400;700&display=swap" rel="stylesheet">
<style>
  :root {
    --stage: #2b2b2b;
    --paper: #f4f0e4;
    --forest: #00753f;
    --sky: #2f7cc4;
    --ink-light: #ffffff;
  }
  html, body {
    margin: 0;
    width: 1200px;
    height: 900px;
    overflow: hidden;
    background: var(--stage);
    font-family: "Lato", Arial, sans-serif;
  }
  .card {
    position: absolute;
    left: 100px;
    top: 165px;
    width: 1000px;
    height: 570px;
    border-radius: 34px;
    overflow: hidden;
    background: var(--paper);
  }
  .card-bands {
    position: absolute;
    inset: 0;
  }
  .brand {
    position: absolute;
    right: 70px;
    top: 58px;
    display: flex;
    align-items: center;
    gap: 16px;
    color: var(--forest);
    font-weight: 700;
    font-size: 46px;
    letter-spacing: 0.5px;
  }
  .brand-dot {
    width: 22px;
    height: 22px;
    border-radius: 50%;
    background: var(--sky);
  }
  .identity {
    position: absolute;
    left: 70px;
    top: 328px;
    color: var(--ink-light);
  }
  .identity-name {
    font-weight: 700;
    font-size: 27px;
    margin: 0 0 6px;
  }
  .identity-role {
    font-size: 18px;
    margin: 0;
    line-height: 1.35;
  }
  .contacts {
    position: absolute;
    left: 70px;
    top: 428px;
    margin: 0;
    padding: 0;
    list-style: none;
    color: var(--ink-light);
    font-size: 18px;
  }
  .contacts li {
    display: flex;
    align-items: center;
    gap: 14px;
    height: 27px;
  }
  .contacts svg {
    width: 20px;
    height: 18px;
    fill: var(--ink-light);
    flex: none;
  }
  .address {
    position: absolute;
    right: 60px;
    bottom: 40px;
    margin: 0;
    color: var(--ink-light);
    font-weight: 700;
    font-size: 19px;
  }
</style>
</head>
<body>
  <article class="card">
    <svg class="card-bands" viewBox="0 0 1000 570" preserveAspectRatio="none" aria-hidden="true">
      <polygon points="0,290 1000,140 1000,156 0,306" fill="var(--sky)"/>
      <polygon points="0,306 1000,156 1000,570 0,570" fill="var(--forest)"/>
    </svg>

    <div class="brand">
      <span class="brand-dot"></span>
      <span class="brand-name">Brightfern Counseling</span>
    </div>

    <div class="identity">
      <p class="identity-name">Gerald M. Whitcombe, Ph.D.</p>
      <p class="identity-role">Licensed Clinical Psychologist<br>Integrative Health Coach</p>
    </div>

    <ul class="contacts">
      <li>
        <svg viewBox="0 0 20 18"><path d="M2 6c0-3 4-4 8-4s8 1 8 4v2h-4V6H6v2H2zM5 9h10l2 8H3z"/></svg>
        770.415.2983
      </li>
      <li>
        <svg viewBox="0 0 20 18"><path d="M5 1h10v5H5zM2 7h16v7h-3v3H5v-3H2zM7 12v4h6v-4z"/></svg>
        770.581.4096
      </li>
      <li>
        <svg viewBox="0 0 20 18"><path d="M1 3h18v12H1zM3 5v.6l7 5 7-5V5l-7 5z"/></svg>
        drgeraldwhitcombe@quillmarsh.net
      </li>
      <li>
        <svg viewBox="0 0 20 18"><path d="M10 1a8 8 0 1 0 0 16a8 8 0 1 0 0-16zM10 2.6c1.3 1.4 2 3.6 2.1 5.6H7.9C8 6.2 8.7 4 10 2.6zM3.7 8.2a6.4 6.4 0 0 1 3-5C6.1 4.7 5.8 6.5 5.7 8.2zM3.7 9.8h2c.1 1.7.4 3.5 1 5a6.4 6.4 0 0 1-3-5zM7.9 9.8h4.2c-.1 2-.8 4.2-2.1 5.6c-1.3-1.4-2-3.6-2.1-5.6zM13.3 14.8c.6-1.5.9-3.3 1-5h2a6.4 6.4 0 0 1-3 5zM14.3 8.2c-.1-1.7-.4-3.5-1-5a6.4 6.4 0 0 1 3 5z"/></svg>
        brightfernwellness.net
      </li>
    </ul>

    <p class="address">4812 Marlowe Ridge Blvd SE, Suite 310, Duluth, GA 30096</p>
  </article>
</body>
</html>
```